Need a website to promote and sell my book

Using images from the book, I need a website designed that helps promote the book and eventually sell it.
*Need a landing page
*About the author page
*Storefront page to purchase
*Coming soon page
*"Featured in" page that can link to news articles etc.
The images posted here are examples, the winner of the contest will get the images from the finished book. I will provide the exact text to the winner of the contest.

I can also provide images of kids reading the book. For now, I'll just use one, the winner can have them all to choose from.
Updates

Extending deadline to allow for a few more designers to submit and to allow time for me to review and hold a poll

Target Market(s)

Parents, aunts, uncles, grandparents, friends who have kids; teachers, daycare teachers, babysitters etc.

Industry/Entity Type

Custom Publishing

Coding

Coded - Design and coding required

Number of Pages Required

5+ page

Font styles to use
Sans Serif

Colors

Designer to choose colors to be used in the design.

Requirements
Must have
• It must have a fun feel like the book.
Nice to have
• Would be great to have a section that automatically pulls tweets about the book into it.

```html
<!DOCTYPE html>
<html lang="en">
<head>
<meta charset="utf-8">
<title>Bright Lab Kids</title>
<link rel="stylesheet" href="https://fonts.googleapis.com/css2?family=Special+Elite&family=Open+Sans:ital,wght@0,400;0,600;0,700;0,800;1,400;1,600&display=swap">
<style>
:root{
  --navy:#0f2147;
  --orange:#d9922b;
  --grey-bg:#efefef;
  --text:#555a63;
  --muted:#8a8f96;
  --white:#ffffff;
  --line:#dcdcdc;
}
*{box-sizing:border-box;margin:0;padding:0}
html,body{width:1200px;height:2892px;overflow:hidden}
body{font-family:"Open Sans",Arial,sans-serif;color:var(--text);background:var(--white);position:relative}
.display{font-family:"Special Elite","Courier New",monospace;color:#1b1b1b}
.btn{display:inline-block;background:var(--orange);color:var(--white);font-size:15px;font-weight:600;letter-spacing:1px;padding:13px 32px;border-radius:26px;text-transform:uppercase;box-shadow:0 2px 6px rgba(0,0,0,.12)}

/* header */
.site-header{position:absolute;top:0;left:0;width:1200px;height:160px;background:var(--white);display:flex;align-items:center;justify-content:space-between;padding:0 72px 0 24px}
.brand{font-size:23px;font-weight:800;color:var(--navy);line-height:1.25;width:260px}
.main-nav{display:flex;align-items:center;gap:40px;font-size:15px;color:var(--muted);text-transform:uppercase;letter-spacing:.5px}
.main-nav .active{color:var(--navy)}
.main-nav .btn{padding:12px 28px}

/* hero */
.hero{position:absolute;top:160px;left:0;width:1200px;height:460px;background:var(--grey-bg)}
.hero h1{position:absolute;left:72px;top:70px;font-size:52px;font-weight:800;color:#1c1c1c}
.hero p{position:absolute;left:72px;top:150px;width:620px;font-size:17px;font-style:italic;font-weight:600;line-height:1.55;color:#555}
.hero-lab{position:absolute;left:72px;top:250px;width:450px;height:186px;border-radius:12px;
  background:
    radial-gradient(circle at 18% 70%,rgba(255,255,255,.55) 0 28px,transparent 30px),
    radial-gradient(circle at 52% 35%,rgba(255,255,255,.45) 0 40px,transparent 42px),
    radial-gradient(circle at 82% 65%,rgba(255,255,255,.5) 0 30px,transparent 32px),
    linear-gradient(120deg,#f6cf78,#ee8a5a 45%,#8cc6e2);
  box-shadow:0 4px 14px rgba(0,0,0,.1)}
.hero-book{position:absolute;left:720px;top:-12px;width:400px;height:452px;border-radius:6px;
  background:
    radial-gradient(ellipse at 50% 30%,rgba(255,255,255,.35),transparent 55%),
    linear-gradient(160deg,#49b7e0,#f2d24a 55%,#e68a3c);
  box-shadow:0 8px 22px rgba(0,0,0,.18)}

/* about */
.about{position:absolute;top:620px;left:0;width:1200px;height:560px}
.about-art{position:absolute;left:80px;top:92px;width:460px;height:448px;border:10px solid #f6d9a2;
  background:
    radial-gradient(circle at 28% 62%,rgba(255,255,255,.45) 0 60px,transparent 62px),
    radial-gradient(circle at 72% 40%,rgba(255,255,255,.35) 0 70px,transparent 72px),
    linear-gradient(150deg,#f7d57a,#f0a84a 60%,#e57b36);
  box-shadow:0 4px 14px rgba(0,0,0,.12)}
.about h2{position:absolute;left:620px;top:152px;font-size:46px}
.about p{position:absolute;left:620px;top:232px;width:520px;font-size:14px;line-height:1.7}
.about .btn{position:absolute;left:620px;top:452px}

/* featured */
.featured{position:absolute;top:1180px;left:0;width:1200px;height:530px}
.section-title{position:absolute;width:1200px;text-align:center;font-size:44px}
.featured .section-title{top:78px}
.book-row{position:absolute;top:170px;left:0;width:1200px}
.book{position:absolute;width:230px;text-align:center}
.book .cover{width:210px;height:210px;margin:0 auto;border-radius:50%;border:8px solid var(--white);box-shadow:0 2px 10px rgba(0,0,0,.25)}
.book .label{margin-top:28px;font-size:20px;font-style:italic;font-weight:600;color:#222;font-family:"Special Elite","Courier New",monospace}
.c1{background:radial-gradient(circle at 50% 45%,#f7c24e 0 22%,#f25a7a 24% 44%,#7a1225 46%)}
.c2{background:radial-gradient(circle at 50% 45%,#f6e27a 0 22%,#f4a44c 24% 44%,#14613b 46%)}
.c3{background:radial-gradient(circle at 50% 45%,#f2d24a 0 22%,#5ac2e8 24% 44%,#0f2a6e 46%)}
.c4{background:radial-gradient(circle at 50% 45%,#7fd3e8 0 22%,#e8a25a 24% 44%,#4e2462 46%)}

/* news */
.news{position:absolute;top:1710px;left:0;width:1200px;height:470px}
.news .section-title{top:30px}
.news-grid{position:absolute;top:130px;left:72px;width:1056px;display:flex;gap:48px}
.news-item{flex:1}
.news-item .date{font-size:12px;font-weight:700;color:#333;letter-spacing:.5px}
.news-item h3{margin-top:26px;font-size:17px;font-weight:700;line-height:1.4;color:var(--orange);text-transform:uppercase}
.news-item p{margin-top:16px;font-size:13px;line-height:1.7;color:var(--muted)}
.news-item .more{display:block;margin-top:22px;font-size:12px;font-weight:800;color:var(--navy);letter-spacing:.5px}
.pager{position:absolute;top:400px;left:0;width:1200px;display:flex;justify-content:center;gap:14px}
.pager span{width:34px;height:34px;border-radius:50%;display:flex;align-items:center;justify-content:center}
.pager .prev{background:var(--navy)}
.pager .next{background:var(--orange)}

/* coming soon */
.coming{position:absolute;top:2180px;left:0;width:1200px;height:420px;background:var(--grey-bg)}
.coming-box{position:absolute;left:80px;top:75px;width:1040px;height:260px;background:var(--white);border:2px solid var(--line)}
.coming h2{position:absolute;left:50px;top:56px;font-size:44px}
.coming p{position:absolute;left:50px;top:124px;width:560px;font-size:14px;line-height:1.7}
.coming .btn{position:absolute;left:50px;top:184px}
.coming-book{position:absolute;left:740px;top:45px;width:320px;height:320px;background:var(--white);padding:28px;box-shadow:0 2px 12px rgba(0,0,0,.15)}
.coming-book div{width:100%;height:100%;
  background:
    radial-gradient(ellipse at 50% 70%,rgba(255,255,255,.35),transparent 55%),
    linear-gradient(160deg,#39b86e,#f2d64b 50%,#3aa0d8)}

/* footer */
.site-footer{position:absolute;top:2600px;left:0;width:1200px;height:292px;background:var(--navy);color:#c8cfdc}
.footer-brand{position:absolute;left:72px;top:62px;font-size:21px;font-weight:800;color:var(--white);line-height:1.3;width:200px}
.footer-col{position:absolute;top:62px}
.footer-col h4{font-family:"Special Elite","Courier New",monospace;font-weight:400;font-size:22px;color:var(--orange)}
.footer-col p{margin-top:12px;font-size:13px;line-height:1.6}
.social{position:absolute;left:930px;top:66px;display:flex;gap:12px}
.social span{width:44px;height:44px;border-radius:50%}
.s1{background:#3b5998}.s2{background:#1877b5}.s3{background:#33aee8}
.copyright{position:absolute;left:0;bottom:0;width:1200px;height:60px;border-top:1px solid #22355e;text-align:center;line-height:60px;font-size:12px;color:#6f7c99}
</style>
</head>
<body>

<header class="site-header">
  <div class="brand">Bright Lab Kids</div>
  <nav class="main-nav">
    <span class="active">Home</span>
    <span>About Us</span>
    <span>Books</span>
    <span>News</span>
    <span>Contact Us</span>
    <span class="btn">Buy Now</span>
  </nav>
</header>

<section class="hero">
  <h1>Lorem ipsum dolor</h1>
  <p>Lorem ipsum dolor sit amet, consectetur adipiscing elit, sed do ad minim veniam, quis nostrud exercitation ullamco laboris.</p>
  <div class="hero-lab" role="img" aria-label="Illustration of children doing experiments around a stack of lab glassware"></div>
  <div class="hero-book" role="img" aria-label="Hands holding the chemistry picture book"></div>
</section>

<section class="about">
  <div class="about-art" role="img" aria-label="Illustrated page from the book about types of change"></div>
  <h2 class="display">About the author</h2>
  <p>Lorem ipsum dolor sit amet, consectetur adipiscing elit, sed do eiusmod tempor incididunt ut labore et dolore magna aliqua. Ut enim ad minim veniam, quis nostrud exercitation ullamco laboris nisi ut aliquip ex ea commodo consequat. Duis aute irure dolor in reprehenderit in voluptate velit esse cillum dolore eu fugiat nulla pariatur. Excepteur sint occaecat cupidatat non proident, sunt in culpa qui officia deserunt mollit anim id est laborum.</p>
  <span class="btn">Buy Now</span>
</section>

<section class="featured">
  <h2 class="section-title display">Featured Books</h2>
  <div class="book-row">
    <div class="book" style="left:77px"><div class="cover c1" role="img" aria-label="Book cover on red"></div><div class="label">Lorem Ipsum</div></div>
    <div class="book" style="left:345px"><div class="cover c2" role="img" aria-label="Book cover on green"></div><div class="label">Lorem Ipsum</div></div>
    <div class="book" style="left:617px"><div class="cover c3" role="img" aria-label="Book cover on blue"></div><div class="label">Lorem Ipsum</div></div>
    <div class="book" style="left:885px"><div class="cover c4" role="img" aria-label="Book cover on purple"></div><div class="label">Lorem Ipsum</div></div>
  </div>
</section>

<section class="news">
  <h2 class="section-title display">Recent News</h2>
  <div class="news-grid">
    <article class="news-item">
      <div class="date">AUG 18</div>
      <h3>Lorem ipsum dolor sit amet, consec tetur adipiscing elit</h3>
      <p>Lorem ipsum dolor sit amet, consectetur adipiscing elit, sed do eiusmod tempor incididunt ut labore et dolore magna aliqua. Ut enim ad minim veniam, quis nostrud exercitation ullamco laboris nisi.</p>
      <span class="more">LEARN MORE</span>
    </article>
    <article class="news-item">
      <div class="date">AUG 18</div>
      <h3>Lorem ipsum dolor sit amet, consec tetur adipiscing elit</h3>
      <p>Lorem ipsum dolor sit amet, consectetur adipiscing elit, sed do eiusmod tempor incididunt ut labore et dolore magna aliqua. Ut enim ad minim veniam, quis nostrud exercitation ullamco laboris nisi.</p>
      <span class="more">LEARN MORE</span>
    </article>
    <article class="news-item">
      <div class="date">AUG 18</div>
      <h3>Lorem ipsum dolor sit amet, consec tetur adipiscing elit</h3>
      <p>Lorem ipsum dolor sit amet, consectetur adipiscing elit, sed do eiusmod tempor incididunt ut labore et dolore magna aliqua. Ut enim ad minim veniam, quis nostrud exercitation ullamco laboris nisi.</p>
      <span class="more">LEARN MORE</span>
    </article>
  </div>
  <div class="pager">
    <span class="prev"><svg width="12" height="12" viewBox="0 0 12 12"><path d="M8 2 4 6l4 4" fill="none" stroke="#fff" stroke-width="2"/></svg></span>
    <span class="next"><svg width="12" height="12" viewBox="0 0 12 12"><path d="M4 2l4 4-4 4" fill="none" stroke="#fff" stroke-width="2"/></svg></span>
  </div>
</section>

<section class="coming">
  <div class="coming-box">
    <h2 class="display">Coming Soon...</h2>
    <p>Lorem ipsum dolor sit amet, consectetur adipiscing elit, sed do eiusmod tempor incididunt ut labore et dolore magna aliqua. Ut enim ad minim veniam.</p>
    <span class="btn">Buy Now</span>
  </div>
  <div class="coming-book"><div role="img" aria-label="Cover of the upcoming chemistry book"></div></div>
</section>

<footer class="site-footer">
  <div class="footer-brand">Bright Lab Kids</div>
  <div class="footer-col" style="left:300px">
    <h4>Address</h4>
    <p>123, Address, State, City,<br>Zipcode</p>
  </div>
  <div class="footer-col" style="left:540px">
    <h4>Phone</h4>
    <p>555.214.0193</p>
  </div>
  <div class="footer-col" style="left:720px">
    <h4>Email</h4>
    <p>hello@brightlabkids.com</p>
  </div>
  <div class="social">
    <span class="s1"></span><span class="s2"></span><span class="s3"></span>
  </div>
  <div class="copyright">Copyright © BRIGHT LAB KIDS 2018. All Rights Reserved</div>
</footer>

</body>
</html>
```